Awesome photographers card for an awesome new business

Double sided business card Black background and silver logo in middle on one side. Details on otherside. please keep it simple

Industry/Entity Type

Photographer

Contact Information for Business Card

Gerald Fenwick
0452817360
GeraldFenwickPhotography47@mailbox.test
www.GeraldFenwickPhotography.test.au
Instagram _Gerald_fenwick

Requirements
Must have
• My logo in Silver
• please use instagram logo instead of "Instagram"

```html
<!DOCTYPE html>
<html lang="en">
<head>
<meta charset="utf-8">
<title>Gerald Fenwick Photography – Business Card</title>
<link href="https://fonts.googleapis.com/css2?family=Montserrat:wght@500;600&family=Open+Sans:wght@400&display=swap" rel="stylesheet">
<style>
  :root {
    --backdrop: #c9c9c9;
    --card-white: #f7f7f7;
    --card-black: #121212;
    --ink: #565656;
    --ink-soft: #5e5e5e;
    --rule: #7a7a7a;
    --silver: #c4c4c4;
    --silver-dark: #8a8a8a;
    --ghost: #ececec;
  }
  * { margin: 0; padding: 0; box-sizing: border-box; }
  html, body { width: 1200px; height: 960px; overflow: hidden; }
  body { background: var(--backdrop); position: relative; font-family: "Open Sans", Arial, sans-serif; }

  .card { position: absolute; width: 600px; height: 342px; border-radius: 14px; overflow: hidden; }
  .card--front { left: 322px; top: 126px; background: var(--card-white); }
  .card--back { left: 320px; top: 502px; background: var(--card-black); }

  .ghost-name {
    position: absolute; left: 20px; top: 150px;
    font-family: "Montserrat", Arial, sans-serif; font-weight: 600;
    font-size: 64px; color: var(--ghost); white-space: nowrap;
  }

  .ribbon {
    position: absolute; left: 421px; top: 0; width: 133px; height: 90px;
    background: linear-gradient(to bottom, #6e6e6e, #b9b9b9 70%, #9c9c9c);
  }
  .badge {
    position: absolute; left: 421px; top: 36px; width: 136px; height: 136px;
    border-radius: 50%; background: var(--card-white); border: 3px solid var(--silver-dark);
    display: flex; align-items: center; justify-content: center; text-align: center;
  }
  .badge-name {
    font-family: "Montserrat", Arial, sans-serif; font-weight: 600;
    font-size: 15px; line-height: 1.25; color: var(--ink); letter-spacing: 1px;
  }

  .holder {
    position: absolute; left: 34px; top: 228px;
    font-family: "Montserrat", Arial, sans-serif; font-weight: 600;
    font-size: 19px; color: var(--ink); letter-spacing: 0.2px;
  }
  .holder-rule { position: absolute; left: 34px; top: 260px; width: 518px; height: 1px; background: var(--rule); }

  .contacts { position: absolute; left: 34px; top: 272px; font-size: 14px; color: var(--ink-soft); line-height: 19px; }
  .contact-row { display: flex; align-items: center; white-space: nowrap; }
  .contact-item { display: inline-flex; align-items: center; margin-right: 6px; }
  .icon { width: 12px; height: 12px; margin-right: 5px; fill: var(--ink-soft); }
  .icon-square { width: 11px; height: 11px; background: var(--ink-soft); margin-right: 5px; border-radius: 2px; }

  .back-badge {
    position: absolute; left: 197px; top: 68px; width: 206px; height: 206px;
    border-radius: 50%; border: 4px solid var(--silver);
    display: flex; align-items: center; justify-content: center; text-align: center;
  }
  .back-badge-name {
    font-family: "Montserrat", Arial, sans-serif; font-weight: 600;
    font-size: 24px; line-height: 1.3; color: var(--silver); letter-spacing: 2px;
  }
</style>
</head>
<body>
  <section class="card card--front" aria-label="Business card front">
    <div class="ghost-name" aria-hidden="true">Gerald Fenwick</div>
    <div class="ribbon"></div>
    <div class="badge"><span class="badge-name">GERALD<br>FENWICK</span></div>

    <h1 class="holder">GERALD FENWICK</h1>
    <div class="holder-rule"></div>

    <div class="contacts">
      <div class="contact-row">
        <span class="contact-item">
          <svg class="icon" viewBox="0 0 24 24"><path d="M6.6 10.8a15.2 15.2 0 0 0 6.6 6.6l2.2-2.2a1 1 0 0 1 1-.25 11.4 11.4 0 0 0 3.6.57 1 1 0 0 1 1 1V20a1 1 0 0 1-1 1A17 17 0 0 1 3 4a1 1 0 0 1 1-1h3.5a1 1 0 0 1 1 1c0 1.25.2 2.45.57 3.57a1 1 0 0 1-.25 1z"/></svg>0452817360
        </span>
        <span class="contact-item">
          <svg class="icon" viewBox="0 0 24 24"><path d="M2 5h20v14H2z M2 5l10 8 10-8" fill="var(--ink-soft)"/><path d="M3 6l9 7 9-7" fill="none" stroke="#f7f7f7" stroke-width="1.6"/></svg>GeraldFenwickPhotography47@mailbox.test
        </span>
      </div>
      <div class="contact-row">
        <span class="contact-item">
          <svg class="icon" viewBox="0 0 24 24"><circle cx="12" cy="12" r="10"/><path d="M2 12h20M12 2c3 3 3 17 0 20M12 2c-3 3-3 17 0 20" fill="none" stroke="#f7f7f7" stroke-width="1.4"/></svg>www.GeraldFenwickPhotography.test.au
        </span>
        <span class="contact-item"><span class="icon-square"></span>_Gerald_fenwick</span>
      </div>
    </div>
  </section>

  <section class="card card--back" aria-label="Business card back">
    <div class="back-badge"><span class="back-badge-name">GERALD<br>FENWICK</span></div>
  </section>
</body>
</html>
```